Brightway Haul & Upkeep Services, are a company that offers a 'one stop shop' pre-move clean up a

I have already selected a logo which I would like on the front of the business cards along with phone numbers, web address and email which are:
0487650392
www.brightwayhaul.com.au
brightwayhaulandupkeep@mailbox.example

On the back of the card I would like to list some of the types of service we offer (clean - move - repairs/maintenance) which are:
CLEAN - windows, gutters, solar panels, driveways/paths, carpets.
MOVE - Small/medium size house/office moves, large item pick-up & delivery, yard clean-up and removal.
General maintenance and repairs.

I would like the blue logo on a gray background.

Thanks

```html
<!DOCTYPE html>
<html lang="en">
<head>
<meta charset="utf-8">
<title>Brightway Haul &amp; Upkeep Services – Business Cards</title>
<link rel="stylesheet" href="https://fonts.googleapis.com/css2?family=Kanit:wght@600&family=Open+Sans:wght@400;600&display=swap">
<style>
  :root {
    --backdrop: #5a3426;
    --card-light: #f4f4f5;
    --card-mid: #d3d4d6;
    --card-dark: #a9abae;
    --brand-blue: #2670bf;
    --ink: #2b2b2d;
    --shadow: rgba(0, 0, 0, 0.45);
  }
  html, body {
    margin: 0;
    padding: 0;
    width: 1200px;
    height: 682px;
    overflow: hidden;
    background: var(--backdrop);
  }
  .canvas {
    position: relative;
    width: 1200px;
    height: 682px;
  }
  .card {
    position: absolute;
    top: 192px;
    width: 520px;
    height: 298px;
    border-radius: 26px;
    background: linear-gradient(160deg, var(--card-dark) 0%, var(--card-mid) 45%, var(--card-light) 100%);
    box-shadow: 0 10px 26px var(--shadow);
    box-sizing: border-box;
    color: var(--ink);
  }
  .card--front { left: 60px; }
  .card--back  { left: 620px; }

  .brand-name {
    font-family: "Kanit", sans-serif;
    font-weight: 600;
    color: var(--brand-blue);
    text-transform: uppercase;
    line-height: 1;
    margin: 0;
    display: flex;
    align-items: center;
    gap: 14px;
  }
  .brand-name__mark {
    width: 18px;
    height: 18px;
    background: var(--brand-blue);
    flex: none;
  }
  .brand-name__lines { display: flex; flex-direction: column; gap: 6px; }
  .brand-name__main { font-size: 50px; letter-spacing: 0.5px; }
  .brand-name__sub  { font-size: 25px; letter-spacing: 0.3px; }

  .card--front .brand-name { position: absolute; left: 46px; top: 44px; }
  .card--back  .brand-name { position: absolute; left: 46px; top: 34px; }

  .contact {
    position: absolute;
    right: 40px;
    top: 180px;
    font-family: "Open Sans", sans-serif;
    text-align: right;
    display: flex;
    flex-direction: column;
    align-items: flex-end;
    gap: 8px;
  }
  .contact__row { display: flex; align-items: center; gap: 7px; }
  .contact__phone { font-size: 19px; }
  .contact__email { font-size: 12.5px; }
  .contact__web { font-size: 13px; letter-spacing: 5px; }
  .contact__icon { width: 15px; height: 15px; flex: none; }

  .services {
    position: absolute;
    left: 46px;
    right: 40px;
    top: 168px;
    font-family: "Open Sans", sans-serif;
  }
  .services__title {
    margin: 0 0 10px;
    font-size: 21px;
    font-weight: 600;
    letter-spacing: 5px;
    color: var(--brand-blue);
    text-align: center;
  }
  .services__list {
    list-style: none;
    margin: 0;
    padding: 0;
    text-align: center;
    font-size: 17px;
    font-weight: 600;
    text-transform: uppercase;
    line-height: 1.6;
  }
  .services__list li::before { content: "• "; }
  .services__inline { display: flex; justify-content: center; gap: 18px; }
  .services__inline span::before { content: "• "; }
</style>
</head>
<body>
<main class="canvas">

  <section class="card card--front" aria-label="Business card front">
    <h1 class="brand-name">
      <span class="brand-name__mark" aria-hidden="true"></span>
      <span class="brand-name__lines">
        <span class="brand-name__main">Brightway Haul</span>
        <span class="brand-name__sub">&amp; Upkeep Services</span>
      </span>
    </h1>
    <div class="contact">
      <div class="contact__row contact__phone">
        <svg class="contact__icon" viewBox="0 0 24 24" aria-hidden="true">
          <circle cx="12" cy="12" r="11" fill="none" stroke="#2b2b2d" stroke-width="2"/>
          <path d="M8.5 6.5c-1 1-1.2 3 .8 6s4.2 4.8 6 4.6l1.4-1.6-2.2-2-1.3.9c-1-.5-2.3-2-2.7-3l1-1.2-1.6-2.5z" fill="#2b2b2d"/>
        </svg>
        <span>0487650392</span>
      </div>
      <div class="contact__row contact__email">
        <svg class="contact__icon" viewBox="0 0 24 24" aria-hidden="true">
          <rect x="2" y="6" width="20" height="13" rx="2" fill="#2b2b2d"/>
          <path d="M3 7l9 7 9-7" fill="none" stroke="#e6e6e7" stroke-width="1.6"/>
        </svg>
        <span>brightwayhaulandupkeep@mailbox.example</span>
      </div>
      <div class="contact__row contact__web">www.brightwayhaul.com.au</div>
    </div>
  </section>

  <section class="card card--back" aria-label="Business card back">
    <h2 class="brand-name">
      <span class="brand-name__mark" aria-hidden="true"></span>
      <span class="brand-name__lines">
        <span class="brand-name__main">Brightway Haul</span>
        <span class="brand-name__sub">&amp; Upkeep Services</span>
      </span>
    </h2>
    <div class="services">
      <p class="services__title">Services we offer</p>
      <ul class="services__list">
        <li class="services__inline" style="list-style:none"><span>Clean</span><span>Move</span></li>
        <li>General maintenance and repairs.</li>
      </ul>
    </div>
  </section>

</main>
</body>
</html>
```